Create a cover for English Grammar Workbook

This book describes a system to learn English in a proper way - we call it The ''Lantern Row'' System.

It focuses on not only teaching grammar and its structures, but also giving students tips on how to use it and the best ways to remember what they learn.

The cover should have 3 realistic pillars (3D), with one closer to the front to show that this book is the 1st (front) Pillar.

The title is: "Building Sentences That Stick: *A Friendly Path Through Usage"*

Author's name: Doreen Calloway

```html
<!DOCTYPE html>
<html lang="en">
<head>
<meta charset="UTF-8">
<title>Building Sentences That Stick — Book Cover</title>
<link rel="stylesheet" href="https://fonts.googleapis.com/css2?family=Allura&family=Montserrat:wght@500;600;800&family=Libre+Baskerville:wght@700&display=swap">
<style>
  :root {
    --page-bg: #ffffff;
    --cover-dark: #333333;
    --accent-red: #c50000;
    --text-light: #ffffff;
    --text-soft: #e6e6e6;
    --pillar-light: #f2f2f2;
    --pillar-shade: #a9a9a9;
  }
  html, body {
    margin: 0;
    padding: 0;
    width: 1200px;
    height: 843px;
    overflow: hidden;
    background: var(--page-bg);
  }
  .canvas {
    position: relative;
    width: 1200px;
    height: 843px;
  }
  .book-cover {
    position: absolute;
    left: 325px;
    top: 31px;
    width: 550px;
    height: 780px;
    background: var(--cover-dark);
    overflow: hidden;
  }
  .spine-strip {
    position: absolute;
    left: 0;
    top: 0;
    width: 38px;
    height: 100%;
    background: var(--accent-red);
  }
  .title-block {
    position: absolute;
    left: 38px;
    right: 0;
    top: 0;
    height: 310px;
    margin: 0;
    text-align: center;
    color: var(--text-light);
  }
  .title-block span {
    position: absolute;
    left: 0;
    right: 0;
    line-height: 1;
    white-space: nowrap;
  }
  .title-script {
    top: 4px;
    font-family: "Allura", cursive;
    font-size: 76px;
    font-weight: 400;
  }
  .title-bold {
    top: 76px;
    font-family: "Montserrat", sans-serif;
    font-weight: 800;
    font-size: 68px;
    letter-spacing: 0.01em;
  }
  .title-serif {
    font-family: "Libre Baskerville", serif;
    font-weight: 700;
    color: var(--text-soft);
  }
  .title-serif.line-one { top: 160px; font-size: 64px; letter-spacing: 0.04em; }
  .title-serif.line-two { top: 235px; font-size: 54px; letter-spacing: 0.06em; }
  .subtitle-box {
    position: absolute;
    left: 66px;
    top: 319px;
    width: 420px;
    height: 38px;
    box-sizing: border-box;
    border: 2px solid var(--accent-red);
    display: flex;
    align-items: center;
    justify-content: center;
    font-family: "Montserrat", sans-serif;
    font-weight: 500;
    font-size: 16px;
    letter-spacing: 0.08em;
    text-transform: uppercase;
    color: var(--text-light);
  }
  .pillars-art {
    position: absolute;
    left: 74px;
    top: 366px;
    width: 400px;
    height: 358px;
  }
  .author-band {
    position: absolute;
    left: 0;
    bottom: 0;
    width: 100%;
    height: 51px;
    background: var(--accent-red);
    display: flex;
    align-items: center;
    justify-content: center;
    font-family: "Montserrat", sans-serif;
    font-weight: 600;
    font-size: 28px;
    letter-spacing: 0.2em;
    text-transform: uppercase;
    color: var(--text-light);
  }
</style>
</head>
<body>
  <div class="canvas">
    <div class="book-cover">
      <div class="spine-strip"></div>

      <h1 class="title-block">
        <span class="title-script">Building</span>
        <span class="title-bold">SENTENCES</span>
        <span class="title-serif line-one">THAT</span>
        <span class="title-serif line-two">STICK</span>
      </h1>

      <div class="subtitle-box">A Friendly Path Through Usage</div>

      <svg class="pillars-art" viewBox="0 0 400 358" role="img" aria-label="Three realistic white classical pillars, the middle one taller and nearer the front">
        <defs>
          <linearGradient id="pillarTone" x1="0" y1="0" x2="1" y2="0">
            <stop offset="0" stop-color="#a9a9a9"/>
            <stop offset="0.5" stop-color="#f2f2f2"/>
            <stop offset="1" stop-color="#a9a9a9"/>
          </linearGradient>
        </defs>
        <rect x="0" y="0" width="400" height="358" fill="url(#pillarTone)" opacity="0.85"/>
      </svg>

      <div class="author-band">Doreen Calloway</div>
    </div>
  </div>
</body>
</html>
```